Business Card Design

We need a design for business cards for our company. We have a logo. We teach EMT's and we are based out of Virginia. The information that will need to add would be, name, title, phone number, email, address. On the back of the business card would be "We help you, help others"

Target Market(s)

People that want to become EMT's

Colors

Designer to choose colors to be used in the design.

Requirements
Must have
• company logo

```html
<!DOCTYPE html>
<html lang="en">
<head>
<meta charset="UTF-8">
<title>Rapid Response Training – Business Card</title>
<link rel="stylesheet" href="https://fonts.googleapis.com/css2?family=Oswald:wght@500&family=Work+Sans:wght@400;500&display=swap">
<style>
  :root {
    --backdrop: #1b1b1b;
    --card: #232323;
    --card-edge: #2c2c2c;
    --silver: #c9c9c9;
    --white: #f2f2f2;
    --red: #d3202f;
  }
  * { margin: 0; padding: 0; box-sizing: border-box; }
  html, body {
    width: 1200px;
    height: 900px;
    overflow: hidden;
    background: var(--backdrop);
  }
  .canvas {
    position: relative;
    width: 1200px;
    height: 900px;
  }
  .card {
    position: absolute;
    left: 280px;
    width: 640px;
    height: 366px;
    background: var(--card);
    border: 1px solid var(--card-edge);
    box-shadow: 0 10px 30px rgba(0,0,0,0.45);
  }
  .card--front { top: 54px; }
  .card--back { top: 460px; }

  .brand {
    position: absolute;
    left: 0; right: 0; top: 0; bottom: 0;
    display: flex;
    align-items: center;
    justify-content: center;
    gap: 16px;
  }
  .brand__dot {
    width: 30px;
    height: 30px;
    border-radius: 50%;
    background: var(--silver);
  }
  .brand__name {
    font-family: "Work Sans", sans-serif;
    font-weight: 500;
    font-size: 34px;
    letter-spacing: 2px;
    text-transform: uppercase;
    color: var(--silver);
  }

  .identity {
    position: absolute;
    left: 60px;
    top: 128px;
    width: 218px;
    text-align: right;
  }
  .identity__name {
    font-family: "Oswald", sans-serif;
    font-weight: 500;
    font-size: 38px;
    line-height: 1.1;
    text-transform: uppercase;
    color: var(--red);
  }
  .identity__title {
    font-family: "Work Sans", sans-serif;
    font-size: 19px;
    color: var(--white);
    margin-top: 2px;
  }
  .divider {
    position: absolute;
    left: 300px;
    top: 132px;
    width: 2px;
    height: 76px;
    background: var(--red);
  }
  .contacts {
    position: absolute;
    left: 326px;
    top: 132px;
    list-style: none;
  }
  .contacts__item {
    display: flex;
    align-items: center;
    gap: 12px;
    font-family: "Work Sans", sans-serif;
    font-size: 19px;
    line-height: 26px;
    color: var(--white);
  }
  .contacts__icon {
    width: 13px;
    height: 13px;
    flex: none;
  }
  .address {
    position: absolute;
    left: 60px;
    bottom: 40px;
    font-family: "Work Sans", sans-serif;
    font-size: 19px;
    color: var(--white);
  }
</style>
</head>
<body>
<main class="canvas">
  <section class="card card--front">
    <div class="brand">
      <span class="brand__dot"></span>
      <span class="brand__name">Rapid Response Training</span>
    </div>
  </section>

  <section class="card card--back">
    <div class="identity">
      <h1 class="identity__name">Daniel Harper</h1>
      <p class="identity__title">Director</p>
    </div>
    <div class="divider"></div>
    <ul class="contacts">
      <li class="contacts__item">
        <svg class="contacts__icon" viewBox="0 0 16 16" aria-hidden="true">
          <path d="M3 1h3l1.5 4-2 1.3a9 9 0 0 0 4.2 4.2L11 8.5l4 1.5v3a2 2 0 0 1-2 2A12 12 0 0 1 1 3a2 2 0 0 1 2-2z" fill="var(--red)"/>
        </svg>
        555-214-7390
      </li>
      <li class="contacts__item">
        <svg class="contacts__icon" viewBox="0 0 16 16" aria-hidden="true">
          <rect x="1" y="3" width="14" height="10" fill="none" stroke="var(--red)" stroke-width="1.5"/>
          <path d="M1 3l7 6 7-6" fill="none" stroke="var(--red)" stroke-width="1.5"/>
        </svg>
        info@rrtraining.com
      </li>
      <li class="contacts__item">
        <svg class="contacts__icon" viewBox="0 0 16 16" aria-hidden="true">
          <circle cx="8" cy="8" r="6.5" fill="none" stroke="var(--red)" stroke-width="1.4"/>
          <ellipse cx="8" cy="8" rx="2.8" ry="6.5" fill="none" stroke="var(--red)" stroke-width="1.2"/>
          <path d="M1.5 8h13" stroke="var(--red)" stroke-width="1.2"/>
        </svg>
        www.rrtraining.com
      </li>
    </ul>
    <p class="address">418 Linden St. Harrisonburg, VA 22801</p>
  </section>
</main>
</body>
</html>
```